Layout for site fence advertising - length approx. 250 cm x 125 cm

The advertising will later be printed on a PVC film and used for events or on sports fields.

Main services :
Your regional contact at
Real estate and business financing
independent insurance advice

```html
<!DOCTYPE html>
<html lang="en">
<head>
<meta charset="utf-8">
<title>Alpenfeld Vermögensberatung – Fence Banner</title>
<link href="https://fonts.googleapis.com/css2?family=Bebas+Neue&family=Lexend:wght@400;500&family=Arimo:wght@700&display=swap" rel="stylesheet">
<style>
  :root {
    --page-bg: #eef1f5;
    --brand-blue: #2d57b5;
    --brand-blue-deep: #23449c;
    --accent-cyan: #3cb6ea;
    --ink-blue: #1f4ea6;
    --white: #ffffff;
  }
  * { margin: 0; padding: 0; box-sizing: border-box; }
  html, body { width: 1117px; height: 1200px; overflow: hidden; background: var(--page-bg); }
  .banner {
    position: absolute; left: 0; top: 321px;
    width: 1117px; height: 559px; overflow: hidden;
    background: linear-gradient(180deg, var(--brand-blue) 0%, var(--brand-blue-deep) 100%);
  }
  .banner-stripes, .contact-band { position: absolute; left: 0; top: 0; }
  .portrait {
    position: absolute; left: 790px; top: 47px; width: 327px; height: 512px;
    border-radius: 150px 150px 0 0;
    background: linear-gradient(180deg, #b98f80 0%, #8a7078 40%, #2c3350 70%, #1d2236 100%);
  }
  .brand { position: absolute; left: 50px; top: 58px; width: 130px; height: 128px; display: flex; align-items: center; }
  .brand-mark { width: 14px; height: 14px; border-radius: 50%; background: var(--white); margin-right: 7px; flex: none; }
  .brand-name { font-family: "Lexend", sans-serif; font-weight: 500; font-size: 22px; color: var(--white); white-space: nowrap; }
  .brand-divider { position: absolute; left: 188px; top: 58px; width: 4px; height: 128px; background: var(--white); }
  .brand-title { position: absolute; left: 200px; top: 84px; font-family: "Lexend", sans-serif; font-weight: 500; color: var(--white); font-size: 24px; white-space: nowrap; }
  .brand-title small { font-size: 17px; }
  .brand-tagline { position: absolute; left: 199px; top: 120px; font-family: "Lexend", sans-serif; font-weight: 500; color: var(--white); font-size: 17px; white-space: nowrap; }
  .label { position: absolute; font-family: "Arimo", sans-serif; font-weight: 700; color: var(--white); font-size: 17px; white-space: nowrap; }
  .label-services { left: 49px; top: 234px; }
  .services-rule { position: absolute; left: 216px; top: 249px; width: 445px; height: 2px; background: var(--white); }
  .service-icon { position: absolute; width: 84px; height: 84px; }
  .service-title { position: absolute; font-family: "Bebas Neue", sans-serif; color: var(--white); font-size: 42px; line-height: 38px; letter-spacing: -0.6px; white-space: nowrap; }
  .label-contact { left: 50px; top: 406px; }
  .phone { position: absolute; left: 50px; top: 462px; display: flex; align-items: center; }
  .phone-icon { width: 52px; height: 54px; margin-right: 9px; }
  .phone-number { font-family: "Bebas Neue", sans-serif; color: var(--ink-blue); font-size: 94px; line-height: 80px; white-space: nowrap; }
</style>
</head>
<body>
  <section class="banner">
    <svg class="banner-stripes" width="1117" height="559" viewBox="0 0 1117 559">
      <polygon points="0,0 170,0 0,170" fill="#3f86d2" opacity="0.55"/>
      <polygon points="230,0 330,0 0,330 0,230" fill="#3a73c9" opacity="0.35"/>
      <polygon points="520,0 640,0 180,460 60,460" fill="#2a4fa8" opacity="0.45"/>
      <polygon points="760,0 900,0 540,360 400,360" fill="#3f7fd0" opacity="0.3"/>
      <polygon points="980,0 1117,0 1117,40 700,460 600,460" fill="#3d8ad6" opacity="0.4"/>
      <polygon points="1117,40 1117,110 930,297 890,260" fill="var(--accent-cyan)"/>
      <polygon points="1117,160 1117,230 1010,337 980,300" fill="#3fa2e2" opacity="0.85"/>
    </svg>

    <div class="portrait" role="img" aria-label="Portrait photo of the regional advisor in a dark suit and white shirt"></div>

    <div class="brand"><span class="brand-mark"></span><span class="brand-name">Alpenfeld</span></div>
    <div class="brand-divider"></div>
    <div class="brand-title">Vermögensberatung <small>GmbH</small></div>
    <div class="brand-tagline">Finanzieren, Versichern, Vorsorgen</div>

    <div class="label label-services">MAIN SERVICES :</div>
    <div class="services-rule"></div>

    <svg class="service-icon" style="left:70px; top:281px" viewBox="0 0 84 84">
      <circle cx="42" cy="42" r="39" fill="none" stroke="#fff" stroke-width="3"/>
      <circle cx="42" cy="42" r="33" fill="#fff"/>
      <g fill="none" stroke="#2d57b5" stroke-width="2" stroke-linejoin="round">
        <polyline points="28,39 42,27 56,39"/>
        <rect x="32" y="37" width="20" height="16"/>
        <rect x="39" y="43" width="6" height="10"/>
        <path d="M25 55 l8 -4 l10 4 l10 -4 l8 4"/>
      </g>
    </svg>
    <div class="service-title" style="left:169px; top:287px">Real estate and<br>business financing</div>

    <svg class="service-icon" style="left:438px; top:281px" viewBox="0 0 84 84">
      <circle cx="42" cy="42" r="39" fill="none" stroke="#fff" stroke-width="3"/>
      <circle cx="42" cy="42" r="33" fill="#fff"/>
      <g fill="none" stroke="#2d57b5" stroke-width="2" stroke-linejoin="round" stroke-linecap="round">
        <path d="M42 25 l11 4 v8 c0 7 -5 11 -11 13 c-6 -2 -11 -6 -11 -13 v-8 z"/>
        <polyline points="37,37 41,41 48,33"/>
        <path d="M27 45 l6 10 h6"/>
        <path d="M57 45 l-6 10 h-6"/>
      </g>
    </svg>
    <div class="service-title" style="left:537px; top:287px">Independent<br>insurance advice</div>

    <svg class="contact-band" width="1117" height="559" viewBox="0 0 1117 559">
      <defs>
        <linearGradient id="bandFade" x1="0" x2="1" y1="0" y2="0">
          <stop offset="0" stop-color="#fff"/>
          <stop offset="0.88" stop-color="#fff"/>
          <stop offset="1" stop-color="#fff" stop-opacity="0"/>
        </linearGradient>
      </defs>
      <polygon points="0,441 368,441 398,410 800,410 800,559 0,559" fill="url(#bandFade)"/>
    </svg>
    <div class="label label-contact">YOUR REGIONAL CONTACT AT</div>

    <div class="phone">
      <svg class="phone-icon" viewBox="0 0 52 56">
        <path d="M10 4 l10 -2 l7 14 l-7 6 c3 8 9 15 17 19 l6 -7 l14 7 l-2 10 c-2 4 -8 6 -14 4 C22 50 6 34 4 16 C3 10 6 6 10 4 z" fill="var(--ink-blue)"/>
      </svg>
      <span class="phone-number">+43 660 123 4567</span>
    </div>
  </section>
</body>
</html>
```